Locksmith Business Cards

My father-in-law is in need of new business cards for his locksmith business and I need to impress him. Kindly help me out!

You can see the previous business card attached. It is a family run business in North Wales.

No individual names on the cards.

Key Things to Feature:
- The words "Prompt", "Local", "Reliable" (as you can see under the logo on the website)
- 24h Emergency Service
- Covering All of North Wales, the Wirral and Chester
- The color blue
- A key or a lock would be interesting (similar to the ones that come up when you google locksmith business card)

Optional (only if design includes bullet points, like the example below):
https://imgvaultcdn.net/samples/208314/55172/55172_3904821_208314_image.jpg
- Residential / Commercial / Automotive
- Alarms & Cameras
- Key Cutting & Safes

https://www.brynhafod-locksmiths.co.uk/

Industry/Entity Type

Locksmith

Contact Information for Business Card

01632 960 418
07700 900 362
brynhafodlocksmiths@mailvane.com
Brynhafod Locksmiths, The Willow Barn, 7 Tannery Rd., Llandudno LL99 4QX
www.brynhafod-locksmiths.co.uk

Requirements
Must have
• - The words "Prompt", "Local", "Reliable" (as you can see under the logo on the website)
• - 24h Emergency Service
• - Covering All of North Wales, the Wirral and Chester
Nice to have
• - A key or a lock would be interesting (similar to the ones that come up when you google locksmith business card)

```html
<!DOCTYPE html>
<html lang="en">
<head>
<meta charset="utf-8">
<title>Brynhafod Locksmiths – Business Cards</title>
<link rel="stylesheet" href="https://fonts.googleapis.com/css2?family=Oswald:wght@500;600&family=Roboto+Condensed:wght@400;700&family=Montserrat:wght@500;600&display=swap">
<style>
  :root {
    --navy: #1e2870;
    --royal: #33449a;
    --mid: #4a5fb5;
    --sky: #5cc3ec;
    --paper: #f6f6f7;
    --ink: #1e2870;
    --ground: #e4e5ea;
  }
  * { box-sizing: border-box; margin: 0; padding: 0; }
  html, body { width: 1200px; height: 1050px; overflow: hidden; }
  body {
    background: var(--ground);
    font-family: "Roboto Condensed", Arial, sans-serif;
    color: var(--ink);
    position: relative;
  }
  .card {
    position: absolute;
    left: 320px;
    width: 560px;
    height: 340px;
    background: var(--paper);
    border-radius: 26px;
    overflow: hidden;
    box-shadow: 0 6px 18px rgba(20, 25, 60, .18);
  }
  .card--front { top: 150px; }
  .card--back { top: 560px; }
  .card svg.shapes { position: absolute; inset: 0; }

  .wordmark {
    position: absolute;
    display: flex;
    align-items: center;
    gap: 12px;
  }
  .wordmark__dot {
    width: 44px; height: 44px;
    border-radius: 50%;
    background: var(--navy);
    flex: none;
  }
  .wordmark__name {
    font-family: "Oswald", sans-serif;
    font-weight: 600;
    color: var(--navy);
    text-transform: uppercase;
    line-height: .95;
    font-size: 34px;
  }
  .card--front .wordmark { left: 40px; top: 150px; }
  .tagline {
    position: absolute;
    left: 40px; top: 232px;
    font-family: "Montserrat", sans-serif;
    font-weight: 500;
    font-size: 11px;
    letter-spacing: 1.2px;
    color: var(--mid);
    white-space: nowrap;
  }
  .services {
    position: absolute;
    right: 26px; top: 52px;
    list-style: none;
    text-align: right;
    color: #fff;
    font-size: 15px;
    line-height: 21px;
  }
  .services li { display: flex; justify-content: flex-end; align-items: center; gap: 12px; }
  .services .bullet { width: 7px; height: 7px; border-radius: 50%; background: var(--sky); }
  .services .bullet--none { background: transparent; }

  .card--back .wordmark { right: 36px; top: 36px; }
  .card--back .wordmark__name { font-size: 30px; }
  .role {
    position: absolute; left: 40px; top: 86px;
    font-family: "Oswald", sans-serif; font-weight: 500;
    font-size: 24px; line-height: 30px; color: var(--mid);
  }
  .address {
    position: absolute; left: 40px; top: 146px;
    font-size: 14px; line-height: 18px; font-weight: 700; color: var(--navy);
  }
  .contacts { position: absolute; left: 40px; top: 194px; list-style: none; font-size: 14px; font-weight: 700; color: var(--navy); }
  .contacts li { display: flex; align-items: center; gap: 10px; height: 18px; }
  .contacts svg { width: 12px; height: 12px; fill: var(--navy); flex: none; }
  .motto {
    position: absolute; right: 22px; top: 236px;
    width: 110px; text-align: center;
    font-family: "Montserrat", sans-serif; font-weight: 600;
    font-size: 14px; line-height: 18px; letter-spacing: 1px; color: #fff;
  }
</style>
</head>
<body>

<section class="card card--front" aria-label="Business card front">
  <svg class="shapes" viewBox="0 0 560 340" aria-hidden="true">
    <circle cx="130" cy="190" r="110" fill="#ebebed"/>
    <path d="M355 0 H560 V340 H420 C300 290 270 80 355 0 Z" fill="var(--royal)"/>
  </svg>
  <div class="wordmark">
    <span class="wordmark__dot"></span>
    <span class="wordmark__name">Brynhafod<br>Locksmiths</span>
  </div>
  <p class="tagline">PROMPT | LOCAL | RELIABLE</p>
  <ul class="services">
    <li>24h Emergency Service <span class="bullet"></span></li>
    <li>Covering All of North Wales, <span class="bullet"></span></li>
    <li>the Wirral and Chester <span class="bullet bullet--none"></span></li>
    <li>Residential / Commercial <span class="bullet"></span></li>
    <li>Automotive <span class="bullet bullet--none"></span></li>
    <li>Alarms &amp; Cameras <span class="bullet"></span></li>
    <li>Key Cutting &amp; Safes <span class="bullet"></span></li>
  </ul>
</section>

<section class="card card--back" aria-label="Business card back">
  <svg class="shapes" viewBox="0 0 560 340" aria-hidden="true">
    <path d="M0 302 C200 314 330 292 390 232 C435 182 485 148 560 134 V150 C488 164 440 198 398 252 C345 314 200 326 0 314 Z" fill="var(--mid)"/>
    <path d="M560 166 C488 180 445 214 404 270 C355 330 210 338 0 328 V340 H560 Z" fill="var(--navy)"/>
    <path d="M0 296 C220 304 330 286 380 236" fill="none" stroke="var(--mid)" stroke-width="2"/>
  </svg>
  <div class="wordmark">
    <span class="wordmark__dot"></span>
    <span class="wordmark__name">Brynhafod<br>Locksmiths</span>
  </div>
  <p class="role">Director</p>
  <p class="address">The Willow Barn, 7 Tannery Rd.,<br>Llandudno LL99 4QX</p>
  <ul class="contacts">
    <li><svg viewBox="0 0 12 12"><path d="M2 1h3l1 3-2 1a7 7 0 0 0 3 3l1-2 3 1v3c-6 1-10-3-9-9z"/></svg>01632 960 418</li>
    <li><svg viewBox="0 0 12 12"><rect x="3" y="0" width="6" height="12" rx="1"/></svg>07700 900 362</li>
    <li><svg viewBox="0 0 12 12"><path d="M0 2h12v8H0z M1 3l5 4 5-4" stroke="#f6f6f7" stroke-width=".8"/></svg>brynhafodlocksmiths@mailvane.com</li>
    <li><svg viewBox="0 0 12 12"><circle cx="6" cy="6" r="5.5"/><path d="M0.5 6h11M6 .5v11" stroke="#f6f6f7" stroke-width=".8"/></svg>www.brynhafod-locksmiths.co.uk</li>
  </ul>
  <p class="motto">PROMPT<br>LOCAL<br>RELIABLE</p>
</section>

</body>
</html>
```